International Travel Technology R&D business needs a wordpress website

We are a start up team of initially 2 individuals but plan to grow our team quickly, we have deep experience in travel technology. Our goal is to provide next generation technology research and development on behalf of our clients who are leading players in the travel technology industry. Attached our logos.

Target Market(s)

Travel Technology companies

Industry/Entity Type

Travel Industry

Coding

Coded - Design and coding required

Font styles to use
Sans Serif

Requirements
Must have
• Make use of our logo and colour scheme in the attached. Has to have a sense of adventure/ stepping into the unknown but equally must convey a sense of professionalism , we are a safe pair of hands. Sample themes are in the attachment .
Nice to have
• We have identified a theme on skinharbor which we feel would be inspirational. We hahe attached them to help in the design as inspiration.
Should not have
• images of airplanes , hotels etc, we want to project a future image.

```html
<!DOCTYPE html>
<html lang="en">
<head>
<meta charset="utf-8">
<title>Nova Transit Labs</title>
<link rel="stylesheet" href="https://fonts.googleapis.com/css2?family=Michroma&family=Oswald:wght@600&family=Open+Sans:wght@300;400;600&family=Noto+Serif&display=swap">
<style>
:root{
  --ink:#1a1a1a;
  --brand:#2e2a7a;
  --accent:#29a8e0;
  --muted:#6e6e6e;
  --white:#ffffff;
  --sky-top:#4ea6cf;
  --sky-mid:#a9cfd9;
  --city:#b6a592;
  --mist:#c7e2ee;
}
*{margin:0;padding:0;box-sizing:border-box}
html,body{width:1200px;height:1200px;overflow:hidden;background:var(--white)}
body{position:relative;font-family:"Open Sans",sans-serif;color:var(--ink)}
.site-header{position:absolute;left:0;top:0;width:1200px;height:100px}
.brand{position:absolute;left:85px;top:36px;display:flex;align-items:center;gap:10px;font-family:"Michroma",sans-serif;font-size:17px;color:var(--brand)}
.brand-dot{width:22px;height:22px;border-radius:50%;background:var(--accent)}
.main-nav a{position:absolute;top:41px;font-family:"Michroma",sans-serif;font-size:13px;color:var(--ink);text-decoration:none;letter-spacing:.5px}
.hero{position:absolute;left:0;top:100px;width:1200px;height:436px;overflow:hidden}
.hero-photo{position:absolute;inset:0;background:linear-gradient(180deg,var(--sky-top) 0%,#7dbcd8 40%,var(--sky-mid) 62%,#c9c2b4 78%,var(--city) 100%)}
.hero-title{position:absolute;left:83px;top:158px;font-family:"Oswald",sans-serif;font-weight:600;font-size:108px;line-height:1;letter-spacing:-3px;transform:scaleX(.86);transform-origin:left;background:linear-gradient(180deg,#fff 20%,rgba(255,255,255,.55));-webkit-background-clip:text;background-clip:text;color:transparent}
.hero-sub{position:absolute;left:85px;top:256px;font-weight:600;font-size:15px;line-height:20px;color:#7f8a8f}
.hero-dots{position:absolute;left:512px;top:396px;display:flex;gap:4px}
.hero-dots span{width:13px;height:13px;border-radius:50%;border:2px solid #111}
.hero-dots span.active{background:#111}
.section-title{position:absolute;left:0;width:1200px;top:594px;text-align:center;font-family:"Michroma",sans-serif;font-size:27px;letter-spacing:1px;color:var(--ink)}
.feature{position:absolute;top:690px;width:190px;text-align:center}
.feature svg{display:block;margin:0 auto;height:60px;width:70px}
.feature h3{margin-top:26px;font-family:"Noto Serif",serif;font-weight:400;font-size:16px;letter-spacing:.5px}
.feature p{margin-top:8px;font-weight:300;font-size:12.3px;line-height:14.6px;color:var(--muted)}
.services{position:absolute;left:0;top:926px;width:1200px;height:274px;overflow:hidden}
.services-photo{position:absolute;inset:0;background:linear-gradient(100deg,var(--mist) 0%,#a9cfe0 45%,#b9d6e4 75%,#9bbdd2 100%)}
.services-panel{position:absolute;left:110px;top:56px;width:878px;height:260px;background:rgba(255,255,255,.18)}
.services-frame{position:absolute;left:18px;top:16px;right:18px;bottom:0;border:1px solid rgba(255,255,255,.8);border-bottom:none}
.services-heading{position:absolute;left:34px;top:82px;font-family:"Michroma",sans-serif;font-size:33px;line-height:38px;color:var(--white)}
.services-intro{position:absolute;left:30px;top:180px;width:230px;font-size:12.5px;line-height:20px;color:#3a4a55}
.services-divider{position:absolute;left:289px;top:70px;width:1px;height:200px;background:rgba(255,255,255,.85)}
.service{position:absolute;top:70px;width:220px}
.service svg{position:absolute;left:-45px;top:0;width:32px;height:30px}
.service h4{font-family:"Noto Serif",serif;font-weight:400;font-size:15.5px;color:#222}
.service p{margin-top:14px;font-size:11.8px;line-height:16.8px;color:#3a4650}
</style>
</head>
<body>
<header class="site-header">
  <div class="brand"><span class="brand-dot"></span>NOVA TRANSIT LABS</div>
  <nav class="main-nav">
    <a href="#" style="left:522px">Home</a>
    <a href="#" style="left:614px">Features</a>
    <a href="#" style="left:734px">Portfolio</a>
    <a href="#" style="left:850px">Service</a>
    <a href="#" style="left:949px">Contact</a>
  </nav>
</header>

<section class="hero">
  <div class="hero-photo" role="img" aria-label="Blurred aerial view of a city skyline under a blue sky"></div>
  <h1 class="hero-title">EXERCITATION</h1>
  <p class="hero-sub">Sed do eiusmod tempor incididunt ut labore et dolore magna aliqua.<br>Ut enim ad minim veniam, quis nostrud</p>
  <div class="hero-dots"><span class="active"></span><span></span><span></span><span></span><span></span></div>
</section>

<h2 class="section-title">EXERCITATION</h2>

<div class="feature" style="left:117px">
  <svg viewBox="0 0 70 60" fill="none" stroke="#29a8e0" stroke-width="2.5"><rect x="3" y="4" width="64" height="40" rx="2"/><path d="M12 32 L24 22 L34 27 L48 14"/><circle cx="24" cy="22" r="2.5" fill="#29a8e0"/><circle cx="34" cy="27" r="2.5" fill="#29a8e0"/><path d="M26 52 L44 52 L40 44 L30 44 Z" fill="#29a8e0"/></svg>
  <h3>EIUSMOD TEMPOR</h3>
  <p>Sed do eiusmod tempor incidi-dunt ut labore et dolore magna aliqua ut enim ad minimvniam, quis nostrud</p>
</div>
<div class="feature" style="left:345px">
  <svg viewBox="0 0 70 60" fill="none" stroke="#29a8e0" stroke-width="2.2"><rect x="14" y="2" width="34" height="54" rx="2"/><path d="M48 6 h4 v52 h-30"/><circle cx="30" cy="12" r="4"/><path d="M20 22 h20 M20 28 h20 M20 34 h20 M20 40 h20 M20 46 h20"/><path d="M58 14 v32 l-2 6 l-2 -6 v-32 z"/></svg>
  <h3>EIUSMOD TEMPOR</h3>
  <p>Sed do eiusmod tempor incidi-dunt ut labore et dolore magna aliqua ut enim ad minimvniam, quis nostrud</p>
</div>
<div class="feature" style="left:570px">
  <svg viewBox="0 0 70 60" fill="none" stroke="#29a8e0" stroke-width="3"><path d="M20 44 c4-4 4-10 4-18 a11 11 0 0 1 22 0 c0 8 0 14 4 18 z"/><path d="M31 48 a4 4 0 0 0 8 0"/><path d="M14 14 a20 20 0 0 0 -2 22 M8 8 a28 28 0 0 0 -3 32 M56 14 a20 20 0 0 1 2 22 M62 8 a28 28 0 0 1 3 32"/></svg>
  <h3>EIUSMOD TEMPOR</h3>
  <p>Sed do eiusmod tempor incidi-dunt ut labore et dolore magna aliqua ut enim ad minimvniam, quis nostrud</p>
</div>
<div class="feature" style="left:791px">
  <svg viewBox="0 0 70 60" fill="none" stroke="#29a8e0" stroke-width="2.2"><path d="M28 2 h14 M31 2 v8 M39 2 v8 M27 10 h16 v6 h-16 z"/><circle cx="35" cy="36" r="19"/><circle cx="35" cy="36" r="14"/><path d="M35 24 v12 h10"/><path d="M4 26 h12 M2 32 h10 M4 38 h12 M54 26 h12 M58 32 h10 M54 38 h12"/></svg>
  <h3>EIUSMOD TEMPOR</h3>
  <p>Sed do eiusmod tempor incidi-dunt ut labore et dolore magna aliqua ut enim ad minimvniam, quis nostrud</p>
</div>

<section class="services">
  <div class="services-photo" role="img" aria-label="Soft blurred city skyline in pale blue haze"></div>
  <div class="services-panel">
    <div class="services-frame"></div>
    <h2 class="services-heading">OUR<br>SERVICES</h2>
    <p class="services-intro">Sed do eiusmod tempor incididunt ut labore et dolore magna aliqua. Ut enim ad minim veniam, quis nostrud</p>
    <div class="services-divider"></div>
    <div class="service" style="left:361px">
      <svg viewBox="0 0 32 30" fill="none" stroke="#333" stroke-width="1.8"><circle cx="16" cy="15" r="4"/><circle cx="4" cy="4" r="2.5" fill="#333"/><circle cx="28" cy="4" r="2.5" fill="#333"/><circle cx="4" cy="26" r="2.5" fill="#333"/><circle cx="28" cy="26" r="2.5" fill="#333"/><circle cx="16" cy="2" r="2" fill="#333"/><path d="M6 6 L13 12 M26 6 L19 12 M6 24 L13 18 M26 24 L19 18 M16 4 V11"/></svg>
      <h4>EIUSMOD TEMPOR</h4>
      <p>Sed do eiusmod tempor incididunt ut labore et dolore magna aliqua. Ut enim ad minim veniam, quis nostrud exercita-tion ullamco laboris nisi ut aliquip ex ea commodo consequat. Duis aute irure</p>
    </div>
    <div class="service" style="left:627px">
      <svg viewBox="0 0 32 30" fill="none" stroke="#333" stroke-width="1.6"><rect x="9" y="2" width="21" height="16"/><circle cx="17" cy="10" r="3"/><path d="M11 18 a6 6 0 0 1 12 0"/><circle cx="6" cy="16" r="3"/><path d="M1 28 a5 5 0 0 1 10 0 M14 24 h16"/></svg>
      <h4>EIUSMOD TEMPOR</h4>
      <p>Sed do eiusmod tempor incididunt ut labore et dolore magna aliqua. Ut enim ad minim veniam, quis nostrud exercita-tion ullamco laboris nisi ut aliquip ex ea commodo consequat. Duis aute irure</p>
    </div>
  </div>
</section>
</body>
</html>
```